FinTech company looking to revamp and expand client-facing interface for our financial models

Pellworth Engines currently has a very simple website that allows clients to interact with our financial models. We are looking to completely redesign the current site and add several extra pages to provide extra functionality. We want the design to have a modern, slick feel, that will work on both a desktop or a tablet. It should be straightforward for clients to move between different pages at any time, and clear from the layout how to interact with the more advanced features. We have included screenshots of existing pages in the attached design brief, as well as sketches of the functionality required by the new pages, but can't provide a direct link to the current site.
Target Market(s)
Professional investors that will be paying to access the interface
Industry/Entity Type
Finance
Number of Pages Required
4 page
Colors
Designer to choose colors to be used in the design.
Look and feel
Each slider illustrates characteristics of the customer's brand and the style your logo design should communicate.

```html
<!DOCTYPE html>
<html lang="en">
<head>
<meta charset="utf-8">
<title>Pellworth Engines – Model Interface</title>
<link rel="stylesheet" href="https://fonts.googleapis.com/css2?family=Open+Sans:wght@600&family=Roboto:wght@400;500&family=Merriweather:wght@400;700&display=swap">
<style>
:root{
  --teal:#16a9c2;
  --cyan:#c3f2f9;
  --grey-col:#efefef;
  --page:#eef1f3;
  --panel-foot:#f4f4f4;
  --ink:#333;
  --nav-top:#3d3d3d;
  --nav-bottom:#121212;
  --link:#1aa3c4;
}
*{box-sizing:border-box;margin:0;padding:0}
html,body{width:1200px;height:2514px;overflow:hidden;background:var(--page)}
.stage{position:relative;width:1230px;height:2576px;transform:scale(0.9756);transform-origin:0 0}
.panel{position:absolute;width:1076px;background:var(--panel-foot);box-shadow:0 10px 30px rgba(0,0,0,.12);font-family:Roboto,sans-serif;color:var(--ink)}
.panel--hero{left:200px;top:197px;height:607px;transform:scale(0.774);transform-origin:0 0;box-shadow:none;background:#fff}
.panel--sectors{left:77px;top:910px;height:755px}
.panel--factors{left:77px;top:1743px;height:755px}
.nav{height:58px;background:linear-gradient(var(--nav-top),var(--nav-bottom));display:flex;align-items:center;color:#fff;position:relative}
.nav__brand{width:170px;height:58px;display:flex;align-items:center;padding-left:28px;font-family:'Open Sans',sans-serif;font-weight:600;font-size:22px;letter-spacing:.3px;border-bottom-left-radius:26px;border-right:1px solid #555}
.nav__tab{height:58px;display:flex;align-items:center;justify-content:center;font-size:16px;border-right:1px solid #555}
.nav__tab--active{background:#151515}
.nav__links{position:absolute;right:26px;top:0;height:58px;display:flex;gap:52px;align-items:center;font-size:16px}
.nav__link{display:flex;align-items:center;gap:6px}
.nav__link svg{width:15px;height:15px;fill:#fff}
.body{margin:0 6px;background:#fff;height:615px;position:relative;padding-top:1px}
.panel--hero .body{height:549px}
.filters{position:absolute;top:28px;left:22px;display:flex;align-items:center}
.filter__small{font-family:Merriweather,serif;font-size:13px;margin-right:20px}
.filter__abs{font-family:Merriweather,serif;font-size:14px;font-weight:700;margin-right:22px}
.filter__abs span{font-weight:400;font-size:13px}
.filter__label{font-weight:500;font-size:16px;color:#111}
.filter__label--stat{font-size:17px;margin-right:10px}
.filter__input{height:41px;border:1px solid #d5d5d5;border-radius:21px;padding-left:14px;display:flex;align-items:center;font-size:16px;color:#777}
.divider{width:1px;height:20px;background:#bbb;margin:0 30px 0 38px}
.divider--narrow{margin:0 18px 0 25px}
.export{position:absolute;top:86px;left:22px;font-family:Merriweather,serif;font-size:15px;color:var(--link);display:flex;align-items:center;gap:7px}
.export svg{width:14px;height:14px;stroke:var(--link);fill:none;stroke-width:2}
.grid{position:absolute;top:121px;left:9px;width:1046px;border-collapse:collapse;table-layout:fixed;font-size:12.5px}
.grid th{background:var(--teal);color:#fff;font-family:Merriweather,serif;font-weight:700;font-size:15px;text-align:left;height:64px;padding-left:16px}
.grid td{height:55px;padding:0 0 0 16px;vertical-align:top;padding-top:12px;line-height:1.5}
.grid tr:nth-child(odd) td{background:var(--cyan)}
.grid td.c-cyan{background:var(--cyan)}
.grid td.c-grey{background:var(--grey-col)}
.grid--factors th.s,.grid--factors td.s{padding-left:42px}
.caret{font-size:9px;vertical-align:2px}
.footer{position:absolute;bottom:28px;left:0;width:100%;text-align:center;font-size:13px;color:#333}
</style>
</head>
<body>
<div class="stage">

<!-- Overview screen -->
<section class="panel panel--hero">
  <nav class="nav">
    <div class="nav__brand">Pellworth</div>
    <div class="nav__tab" style="width:92px">QCORE</div>
    <div class="nav__tab nav__tab--active" style="width:71px">250D</div>
    <div class="nav__tab" style="width:70px">83D</div>
    <div class="nav__tab" style="width:73px">42D</div>
    <div class="nav__links">
      <span class="nav__link"><svg viewBox="0 0 16 16"><path d="M8 1 0 8h2v7h4v-5h4v5h4V8h2z"/></svg>Model</span>
      <span class="nav__link"><svg viewBox="0 0 16 16"><path d="M8 5a3 3 0 1 0 0 6 3 3 0 0 0 0-6zm6.5 4.2V6.8l-1.8-.4-.5-1.2 1-1.6-1.6-1.6-1.6 1-1.2-.5L8.4.5H6.8l-.4 1.8-1.2.5-1.6-1-1.6 1.6 1 1.6-.5 1.2-1.8.4v2.4l1.8.4.5 1.2-1 1.6 1.6 1.6 1.6-1 1.2.5.4 1.8h2.4l.4-1.8 1.2-.5 1.6 1 1.6-1.6-1-1.6.5-1.2z"/></svg>Sensitivities</span>
      <span class="nav__link"><svg viewBox="0 0 16 16"><path d="M8 .5l2.3 5 5.4.5-4.1 3.6 1.2 5.3L8 12.1l-4.8 2.8 1.2-5.3L.3 6l5.4-.5z"/></svg>Favourites</span>
    </div>
  </nav>
  <div class="body">
    <div class="filters">
      <span class="filter__small">Quality</span><span class="filter__label">Threshold :</span>
      <span class="filter__input" style="width:198px;padding-left:2px">-10</span>
      <span class="divider"></span>
      <span class="filter__abs">Abs.<span>Stat</span></span><span class="filter__label">Threshold :</span>
      <span class="filter__input" style="width:198px;padding-left:2px">-10</span>
    </div>
    <div class="export"><svg viewBox="0 0 16 16"><path d="M12 9v5H2V4h5M10 1h5v5M15 1 7 9"/></svg>EXPORT</div>
    <table class="grid">
      <colgroup><col style="width:74px"><col style="width:104px"><col style="width:89px"><col style="width:99px"><col style="width:88px"><col style="width:88px"><col style="width:88px"><col style="width:88px"><col style="width:88px"><col style="width:88px"><col style="width:88px"><col style="width:64px"></colgroup>
      <tr><th>ID <span class="caret">▼</span></th><th>Sector</th><th>Time</th><th>Quality</th><th>Stat 1</th><th>Stat 2</th><th>Stat 3</th><th>Stat 4</th><th>Stat 5</th><th>Stat 6</th><th>Stat 7</th><th>Stat 8</th></tr>
      <tr><td class="c-cyan">Model 1</td><td class="c-grey">Materials</td><td class="c-cyan">2019-07-03<br>12:15:00.000</td><td>30.2288</td><td>2.01574</td><td>23.305</td><td>-0.149368</td><td>22.3054</td><td>4.63714</td><td>0.945706</td><td>2.81949</td><td>2.60858</td></tr>
      <tr><td class="c-cyan">Model 2</td><td class="c-grey">Industrials</td><td class="c-cyan">2019-07-03<br>12:15:00.000</td><td>32.8694</td><td>0.87307</td><td>32.185</td><td>-0.0336927</td><td>33.9911</td><td>11.5693</td><td>-0.472968</td><td>-0.830458</td><td>6.80646</td></tr>
      <tr><td class="c-cyan">Model 3</td><td class="c-grey">Consumer Discretionary</td><td class="c-cyan">2019-07-03<br>12:15:00.000</td><td>1.66002</td><td>-0.569222</td><td>159.814</td><td>0.0252328</td><td>172.616</td><td>10.2875</td><td>-0.750396</td><td>-0.385309</td><td>4.69146</td></tr>
      <tr><td class="c-cyan">Model 4</td><td class="c-grey">Information Technology</td><td class="c-cyan">2019-07-03<br>12:15:00.000</td><td>45.6856</td><td>0.412148</td><td>202.488</td><td>0.00849232</td><td>205.834</td><td>11.9094</td><td>-0.137913</td><td>0.449595</td><td>3.85106</td></tr>
      <tr><td class="c-cyan">Model 5</td><td class="c-grey">Information Technology</td><td class="c-cyan">2019-07-03<br>12:15:00.000</td><td>75.7733</td><td>7.06728</td><td>188.605</td><td>0.016913</td><td>181.665</td><td>3.82241</td><td>0.981019</td><td>1.29847</td><td>3.34927</td></tr>
    </table>
  </div>
</section>

<!-- Sector models page -->
<section class="panel panel--sectors">
  <nav class="nav">
    <div class="nav__brand">Pellworth</div>
    <div class="nav__tab" style="width:92px">QCORE</div>
    <div class="nav__tab nav__tab--active" style="width:71px">250D</div>
    <div class="nav__tab" style="width:70px">83D</div>
    <div class="nav__tab" style="width:73px">42D</div>
    <div class="nav__links">
      <span class="nav__link"><svg viewBox="0 0 16 16"><path d="M8 1 0 8h2v7h4v-5h4v5h4V8h2z"/></svg>Model</span>
      <span class="nav__link"><svg viewBox="0 0 16 16"><path d="M8 5a3 3 0 1 0 0 6 3 3 0 0 0 0-6zm6.5 4.2V6.8l-1.8-.4-.5-1.2 1-1.6-1.6-1.6-1.6 1-1.2-.5L8.4.5H6.8l-.4 1.8-1.2.5-1.6-1-1.6 1.6 1 1.6-.5 1.2-1.8.4v2.4l1.8.4.5 1.2-1 1.6 1.6 1.6 1.6-1 1.2.5.4 1.8h2.4l.4-1.8 1.2-.5 1.6 1 1.6-1.6-1-1.6.5-1.2z"/></svg>Sensitivities</span>
      <span class="nav__link"><svg viewBox="0 0 16 16"><path d="M8 .5l2.3 5 5.4.5-4.1 3.6 1.2 5.3L8 12.1l-4.8 2.8 1.2-5.3L.3 6l5.4-.5z"/></svg>Favourites</span>
    </div>
  </nav>
  <div class="body">
    <div class="filters">
      <span class="filter__small">Quality</span><span class="filter__label">Threshold :</span>
      <span class="filter__input" style="width:198px;padding-left:2px">-10</span>
      <span class="divider"></span>
      <span class="filter__abs">Abs.<span>Stat</span></span><span class="filter__label">Threshold :</span>
      <span class="filter__input" style="width:198px;padding-left:2px">-10</span>
    </div>
    <div class="export"><svg viewBox="0 0 16 16"><path d="M12 9v5H2V4h5M10 1h5v5M15 1 7 9"/></svg>EXPORT</div>
    <table class="grid">
      <colgroup><col style="width:74px"><col style="width:104px"><col style="width:89px"><col style="width:99px"><col style="width:88px"><col style="width:88px"><col style="width:88px"><col style="width:88px"><col style="width:88px"><col style="width:88px"><col style="width:88px"><col style="width:64px"></colgroup>
      <tr><th>ID <span class="caret">▼</span></th><th>Sector</th><th>Time</th><th>Quality</th><th>Stat 1</th><th>Stat 2</th><th>Stat 3</th><th>Stat 4</th><th>Stat 5</th><th>Stat 6</th><th>Stat 7</th><th>Stat 8</th></tr>
      <tr><td class="c-cyan">Model 1</td><td class="c-grey">Materials</td><td class="c-cyan">2019-07-03<br>12:15:00.000</td><td>30.2288</td><td>2.01574</td><td>23.305</td><td>-0.149368</td><td>22.3054</td><td>4.63714</td><td>0.945706</td><td>2.81949</td><td>2.60858</td></tr>
      <tr><td class="c-cyan">Model 2</td><td class="c-grey">Industrials</td><td class="c-cyan">2019-07-03<br>12:15:00.000</td><td>32.8694</td><td>0.87307</td><td>32.185</td><td>-0.0336927</td><td>33.9911</td><td>11.5693</td><td>-0.472968</td><td>-0.830458</td><td>6.80646</td></tr>
      <tr><td class="c-cyan">Model 3</td><td class="c-grey">Consumer Discretionary</td><td class="c-cyan">2019-07-03<br>12:15:00.000</td><td>1.66002</td><td>-0.569222</td><td>159.814</td><td>0.0252328</td><td>172.616</td><td>10.2875</td><td>-0.750396</td><td>-0.385309</td><td>4.69146</td></tr>
      <tr><td class="c-cyan">Model 4</td><td class="c-grey">Information Technology</td><td class="c-cyan">2019-07-03<br>12:15:00.000</td><td>45.6856</td><td>0.412148</td><td>202.488</td><td>0.00849232</td><td>205.834</td><td>11.9094</td><td>-0.137913</td><td>0.449595</td><td>3.85106</td></tr>
      <tr><td class="c-cyan">Model 5</td><td class="c-grey">Information Technology</td><td class="c-cyan">2019-07-03<br>12:15:00.000</td><td>75.7733</td><td>7.06728</td><td>188.605</td><td>0.016913</td><td>181.665</td><td>3.82241</td><td>0.981019</td><td>1.29847</td><td>3.34927</td></tr>
    </table>
  </div>
  <p class="footer">© 2019 Copyrights. The Company name . All rights reserved</p>
</section>

<!-- Factor sensitivities page -->
<section class="panel panel--factors">
  <nav class="nav">
    <div class="nav__brand">Pellworth</div>
    <div class="nav__tab" style="width:92px">QCORE</div>
    <div class="nav__tab nav__tab--active" style="width:71px">250D</div>
    <div class="nav__tab" style="width:70px">83D</div>
    <div class="nav__tab" style="width:73px">42D</div>
    <div class="nav__links">
      <span class="nav__link"><svg viewBox="0 0 16 16"><path d="M8 1 0 8h2v7h4v-5h4v5h4V8h2z"/></svg>Model</span>
      <span class="nav__link"><svg viewBox="0 0 16 16"><path d="M8 5a3 3 0 1 0 0 6 3 3 0 0 0 0-6zm6.5 4.2V6.8l-1.8-.4-.5-1.2 1-1.6-1.6-1.6-1.6 1-1.2-.5L8.4.5H6.8l-.4 1.8-1.2.5-1.6-1-1.6 1.6 1 1.6-.5 1.2-1.8.4v2.4l1.8.4.5 1.2-1 1.6 1.6 1.6 1.6-1 1.2.5.4 1.8h2.4l.4-1.8 1.2-.5 1.6 1 1.6-1.6-1-1.6.5-1.2z"/></svg>Sensitivities</span>
      <span class="nav__link"><svg viewBox="0 0 16 16"><path d="M8 .5l2.3 5 5.4.5-4.1 3.6 1.2 5.3L8 12.1l-4.8 2.8 1.2-5.3L.3 6l5.4-.5z"/></svg>Favourites</span>
    </div>
  </nav>
  <div class="body">
    <div class="filters" style="left:23px">
      <span class="filter__label filter__label--stat">Stat 1 Threshold</span><span class="filter__input" style="width:160px">-10</span>
      <span class="divider divider--narrow"></span>
      <span class="filter__label filter__label--stat">Stat 1 Threshold</span><span class="filter__input" style="width:160px">-10</span>
      <span class="divider divider--narrow"></span>
      <span class="filter__label filter__label--stat">Stat 1 Threshold</span><span class="filter__input" style="width:160px">-10</span>
    </div>
    <div class="export"><svg viewBox="0 0 16 16"><path d="M12 9v5H2V4h5M10 1h5v5M15 1 7 9"/></svg>EXPORT</div>
    <table class="grid grid--factors">
      <colgroup><col style="width:103px"><col style="width:123px"><col style="width:120px"><col style="width:112px"><col style="width:112px"><col style="width:122px"><col style="width:112px"><col style="width:112px"><col style="width:130px"></colgroup>
      <tr><th>Factor</th><th>ID <span class="caret">▼</span></th><th>Time</th><th class="s">Stat 1</th><th class="s">Stat 2</th><th class="s">Stat 3</th><th class="s">Stat 4</th><th class="s">Stat 5</th><th class="s">Stat 6</th></tr>
      <tr><td class="c-cyan">Factor 1</td><td class="c-grey">Model 1</td><td class="c-cyan">Materials</td><td class="s">-1.4</td><td class="s">0.1</td><td class="s">-3.1</td><td class="s">0.7</td><td class="s">30.2</td><td class="s">0.9</td></tr>
      <tr><td class="c-cyan">Factor 2</td><td class="c-grey">Model 1</td><td class="c-cyan">Materials</td><td class="s">2.8</td><td class="s">0.1</td><td class="s">6.1</td><td class="s">100</td><td class="s">30.2</td><td class="s">0.9</td></tr>
      <tr><td class="c-cyan">Factor 3</td><td class="c-grey">Model 1</td><td class="c-cyan">Materials</td><td class="s">-3.7</td><td class="s">2.7</td><td class="s">-7.2</td><td class="s">100</td><td class="s">30.2</td><td class="s">0.9</td></tr>
      <tr><td class="c-cyan">Factor 1</td><td class="c-grey">Model 2</td><td class="c-cyan">Industrials</td><td class="s">2.8</td><td class="s">0.2</td><td class="s">2.7</td><td class="s">0.5</td><td class="s">32.9</td><td class="s">-0.5</td></tr>
      <tr><td class="c-cyan">Factor 2</td><td class="c-grey">Model 2</td><td class="c-cyan">Industrials</td><td class="s">0.8</td><td class="s">0.3</td><td class="s">2.5</td><td class="s">0.5</td><td class="s">32.9</td><td class="s">-0.5</td></tr>
    </table>
  </div>
  <p class="footer">© 2019 Copyrights. The Company name . All rights reserved</p>
</section>

</div>
</body>
</html>
```